Kestrel Facilities Business Card Design

We would now like to design business cards with the new Kestrel Facilities logo

Target Market(s)

Professional

Industry/Entity Type

Professional services

Contact Information for Business Card

Employee name, title, phone number, email address, corporate office address and logo.

Font styles to use
Sans Serif

Colors
0054AA
0677BA
7BADD7
CADEEF
E8F1F8

Requirements
Must have
• My logo
Should not have
• any other pictures or images besides my logo

```html
<!DOCTYPE html>
<html lang="en">
<head>
<meta charset="utf-8">
<title>Kestrel Facilities Business Card</title>
<link rel="stylesheet" href="https://fonts.googleapis.com/css2?family=Montserrat:wght@400;500;700&display=swap">
<style>
  :root {
    --brand-blue: #3878c1;
    --ink: #1c1c1c;
    --card: #ffffff;
    --backdrop: #8c8c8c;
  }
  * { margin: 0; padding: 0; box-sizing: border-box; }
  html, body {
    width: 1160px;
    height: 1200px;
    overflow: hidden;
    background: var(--backdrop);
    font-family: "Montserrat", Arial, sans-serif;
  }
  .canvas { position: relative; width: 1160px; height: 1200px; }
  .card {
    position: absolute;
    left: 199px;
    width: 778px;
    background: var(--card);
  }
  .card--front { top: 105px; height: 442px; }
  .card--back  { top: 634px; height: 444px; }

  .brand {
    position: absolute;
    display: flex;
    align-items: center;
    color: var(--brand-blue);
    font-weight: 700;
    line-height: 1.05;
  }
  .brand__square {
    flex: none;
    background: var(--brand-blue);
  }
  .card--front .brand { left: 31px; top: 86px; gap: 14px; font-size: 34px; }
  .card--front .brand__square { width: 56px; height: 56px; }
  .card--back .brand {
    left: 0; right: 0; top: 0; bottom: 0;
    justify-content: center; gap: 22px; font-size: 58px;
  }
  .card--back .brand__square { width: 96px; height: 96px; }

  .address {
    position: absolute;
    left: 28px;
    top: 230px;
    font-size: 19.5px;
    line-height: 29px;
    color: var(--ink);
    font-style: normal;
  }
  .contacts {
    position: absolute;
    left: 28px;
    top: 322px;
    list-style: none;
    font-size: 19.5px;
    line-height: 29.5px;
    color: var(--ink);
  }
  .contacts li { display: flex; align-items: center; gap: 8px; }
  .contacts svg { width: 19px; height: 19px; flex: none; }

  .person {
    position: absolute;
    right: 41px;
    top: 207px;
    text-align: right;
  }
  .person__name {
    font-size: 30px;
    font-weight: 700;
    color: var(--brand-blue);
    line-height: 36px;
    letter-spacing: -0.3px;
  }
  .person__title {
    font-size: 21px;
    color: var(--ink);
    line-height: 26px;
  }
  .accent-bar {
    position: absolute;
    left: 753px;
    top: 212px;
    width: 25px;
    height: 55px;
    background: var(--brand-blue);
  }
</style>
</head>
<body>
<main class="canvas">
  <section class="card card--front">
    <div class="brand">
      <span class="brand__square"></span>
      <span class="brand__name">Kestrel<br>Facilities</span>
    </div>

    <address class="address">
      P.O Box 4418-00300<br>
      Nairobi, Kenya
    </address>

    <ul class="contacts">
      <li>
        <svg viewBox="0 0 20 20" aria-hidden="true">
          <path fill="var(--brand-blue)" d="M2 7c0-2 3-4 8-4s8 2 8 4v2h-4V7H6v2H2z"/>
          <rect x="4" y="9" width="12" height="8" rx="1" fill="var(--brand-blue)"/>
          <g fill="#fff"><rect x="7" y="11" width="1.5" height="1.5"/><rect x="9.3" y="11" width="1.5" height="1.5"/><rect x="11.6" y="11" width="1.5" height="1.5"/><rect x="7" y="13.5" width="1.5" height="1.5"/><rect x="9.3" y="13.5" width="1.5" height="1.5"/><rect x="11.6" y="13.5" width="1.5" height="1.5"/></g>
        </svg>
        <span>+254-160-44721</span>
      </li>
      <li>
        <svg viewBox="0 0 20 20" aria-hidden="true">
          <rect x="1" y="4" width="18" height="12" fill="var(--brand-blue)"/>
          <path d="M1.5 4.5 10 11l8.5-6.5M1.5 15.5l6-5M18.5 15.5l-6-5" stroke="#fff" stroke-width="1.2" fill="none"/>
        </svg>
        <span>info@kestrelfacilities.com</span>
      </li>
      <li>
        <svg viewBox="0 0 20 20" aria-hidden="true">
          <circle cx="10" cy="10" r="8.5" fill="var(--brand-blue)"/>
          <path d="M5 6c2 0 3 1 3 3s-2 2-2 4M12 4c0 2 2 2 3 3M11 17c0-2 2-3 4-3" stroke="#fff" stroke-width="1.5" fill="none" stroke-linecap="round"/>
        </svg>
        <span>www.kestrelfacilities.com</span>
      </li>
    </ul>

    <div class="person">
      <p class="person__name">WANJIRU KAMAU</p>
      <p class="person__title">Co-Founder</p>
    </div>
    <span class="accent-bar"></span>
  </section>

  <section class="card card--back">
    <div class="brand">
      <span class="brand__square"></span>
      <span class="brand__name">Kestrel<br>Facilities</span>
    </div>
  </section>
</main>
</body>
</html>
```